Bramwell Crest Electric van design

Looking to design a wrap for a 2021 varenta cargolux high roof using orange black and dark grey colors like in the logo

```html
<!DOCTYPE html>
<html lang="en">
<head>
<meta charset="utf-8">
<title>Bramwell Crest Electric – Van Wrap</title>
<link rel="stylesheet" href="https://fonts.googleapis.com/css2?family=Montserrat:wght@600;700&display=swap">
<style>
  :root {
    --wrap-orange: #e8613a;
    --wrap-black: #262626;
    --wrap-grey: #3a3c40;
    --wrap-white: #ffffff;
    --page-bg: #e9ebee;
    --panel-line: #d3d6da;
  }
  html, body {
    margin: 0;
    padding: 0;
    width: 1200px;
    height: 3047px;
    overflow: hidden;
    background: var(--page-bg);
  }
  .wrap-sheet {
    width: 1200px;
    height: 3047px;
    display: flex;
    flex-direction: column;
  }
  .view {
    display: block;
    width: 1200px;
  }
  .view--side { height: 606px; }
  .view--rear { height: 1029px; }
  .view--front { height: 806px; }
  .brand-name {
    font-family: "Montserrat", sans-serif;
    font-weight: 600;
    fill: var(--wrap-black);
  }
  .brand-name--light { fill: var(--wrap-white); }
  .phone-number {
    font-family: "Montserrat", sans-serif;
    font-weight: 700;
    fill: var(--wrap-white);
  }
  .web-address {
    font-family: "Montserrat", sans-serif;
    font-weight: 600;
    fill: var(--wrap-white);
  }
  .body-panel { fill: var(--wrap-white); stroke: var(--panel-line); stroke-width: 2; }
  .black-field { fill: var(--wrap-black); }
  .grey-field { fill: var(--wrap-grey); }
  .orange-band { fill: var(--wrap-orange); }
  .brand-disc { fill: var(--wrap-orange); }
  .brand-disc-ring { fill: none; stroke: var(--wrap-white); stroke-width: 3; }
</style>
</head>
<body>
<main class="wrap-sheet">

  <!-- Driver side (rear of van on the left) -->
  <svg class="view view--side" viewBox="0 0 1200 606" aria-label="Driver side wrap layout">
    <defs>
      <clipPath id="side-left-body">
        <path d="M90 80 Q95 62 130 62 L930 62 Q1000 70 1050 200 L1130 330 Q1140 380 1130 440 L1120 480 L70 480 L70 110 Z"/>
      </clipPath>
    </defs>
    <path class="body-panel" d="M90 80 Q95 62 130 62 L930 62 Q1000 70 1050 200 L1130 330 Q1140 380 1130 440 L1120 480 L70 480 L70 110 Z"/>
    <g clip-path="url(#side-left-body)">
      <path class="black-field" d="M60 50 L270 50 A270 270 0 0 1 390 225 L390 330 Q370 380 270 385 L60 385 Z"/>
      <path class="orange-band" d="M340 318 L800 318 L865 450 L800 450 L742 378 L270 380 Z"/>
      <path class="black-field" d="M270 385 L740 385 Q760 395 770 410 L770 430 L60 430 L60 385 Z"/>
      <path class="orange-band" d="M780 455 L880 455 L905 495 L805 495 Z"/>
      <rect class="grey-field" x="60" y="430" width="1100" height="60"/>
    </g>
    <circle class="brand-disc" cx="218" cy="218" r="124"/>
    <circle class="brand-disc-ring" cx="218" cy="218" r="114"/>
    <text class="brand-name" x="404" y="218" font-size="33" letter-spacing="3">BRAMWELL CREST</text>
    <text class="brand-name" x="404" y="262" font-size="40">Electric</text>
    <text class="phone-number" x="420" y="364" font-size="30">555.014.2290</text>
  </svg>

  <!-- Passenger side (front of van on the left) -->
  <svg class="view view--side" viewBox="0 0 1200 606" aria-label="Passenger side wrap layout">
    <defs>
      <clipPath id="side-right-body">
        <path d="M1110 80 Q1105 62 1070 62 L270 62 Q200 70 150 200 L70 330 Q60 380 70 440 L80 480 L1130 480 L1130 110 Z"/>
      </clipPath>
    </defs>
    <path class="body-panel" d="M1110 80 Q1105 62 1070 62 L270 62 Q200 70 150 200 L70 330 Q60 380 70 440 L80 480 L1130 480 L1130 110 Z"/>
    <g clip-path="url(#side-right-body)">
      <path class="black-field" d="M1140 50 L930 50 A270 270 0 0 0 810 225 L810 330 Q830 380 930 385 L1140 385 Z"/>
      <path class="orange-band" d="M860 318 L400 318 L335 450 L400 450 L458 378 L930 380 Z"/>
      <path class="black-field" d="M930 385 L460 385 Q440 395 430 410 L430 430 L1140 430 L1140 385 Z"/>
      <path class="orange-band" d="M420 455 L320 455 L295 495 L395 495 Z"/>
      <rect class="grey-field" x="40" y="430" width="1100" height="60"/>
    </g>
    <circle class="brand-disc" cx="982" cy="218" r="124"/>
    <circle class="brand-disc-ring" cx="982" cy="218" r="114"/>
    <text class="brand-name" x="798" y="218" font-size="33" letter-spacing="3" text-anchor="end">BRAMWELL CREST</text>
    <text class="brand-name" x="798" y="262" font-size="40" text-anchor="end">Electric</text>
    <text class="phone-number" x="668" y="364" font-size="30" text-anchor="middle">555.014.2290</text>
  </svg>

  <!-- Rear doors -->
  <svg class="view view--rear" viewBox="0 0 1200 1029" aria-label="Rear doors wrap layout">
    <path class="black-field" d="M345 110 Q350 90 380 90 L820 90 Q850 90 855 110 L905 480 L905 790 L295 790 L295 480 Z"/>
    <line x1="600" y1="90" x2="600" y2="790" stroke="#1a1a1a" stroke-width="2"/>
    <circle class="brand-disc" cx="600" cy="220" r="78"/>
    <circle class="brand-disc-ring" cx="600" cy="220" r="72"/>
    <text class="brand-name brand-name--light" x="600" y="370" font-size="50" letter-spacing="4" text-anchor="middle">BRAMWELL CREST</text>
    <text class="brand-name brand-name--light" x="600" y="430" font-size="56" text-anchor="middle">Electric</text>
    <path class="orange-band" d="M385 448 L818 448 L806 502 L392 502 Z"/>
    <text class="phone-number" x="600" y="491" font-size="50" text-anchor="middle">555.014.2290</text>
    <text class="web-address" x="600" y="645" font-size="24" text-anchor="middle">bramwellcrestelectric.com</text>
  </svg>

  <!-- Hood / front -->
  <svg class="view view--front" viewBox="0 0 1200 806" aria-label="Hood wrap layout">
    <path class="body-panel" d="M285 360 L915 360 Q960 370 980 430 L990 560 L210 560 L220 430 Q240 370 285 360 Z"/>
    <path class="orange-band" d="M280 362 L345 362 Q310 450 345 548 L268 548 Q240 450 280 362 Z"/>
    <path class="orange-band" d="M920 362 L855 362 Q890 450 855 548 L932 548 Q960 450 920 362 Z"/>
    <path class="black-field" d="M330 362 L870 362 Q905 450 870 548 L330 548 Q295 450 330 362 Z"/>
    <circle class="brand-disc" cx="443" cy="460" r="50"/>
    <circle class="brand-disc-ring" cx="443" cy="460" r="45"/>
    <text class="brand-name brand-name--light" x="513" y="452" font-size="30" letter-spacing="2.5">BRAMWELL CREST</text>
    <text class="brand-name brand-name--light" x="513" y="496" font-size="38">Electric</text>
  </svg>

</main>
</body>
</html>
```